New Innovative Counselling and psychotherapy Service needs Business Card design

Keep it simple and professional. On one side, just company name and logo (perhaps in all blue) and maybe a tag line.

On other side (all white) my name and Qualifications in centre

Industry/Entity Type

Health And Wellness

Contact Information for Business Card

Dara Whelby
Counsellor & Psychotherapist
BSc (Psychol.), BA, Dip. (Couns. & Psych.), PG.Cert (CBT), FGTrK, ONRE

I will also require Mobile no, Email and web site address of which I'll pass on to final designer.

Font styles to use
Sans Serif

Requirements
Must have
• My Logo Only and please use the colours in logo that is in it.
Should not have
• Any other images

```html
<!DOCTYPE html>
<html lang="en">
<head>
<meta charset="utf-8">
<title>Thrive Lane – Business Card</title>
<link href="https://fonts.googleapis.com/css2?family=Lato:ital,wght@0,400;0,700;1,700&family=Raleway:wght@400&display=swap" rel="stylesheet">
<style>
  :root {
    --sky: #4fb1e3;
    --sky-faint: #eef6fc;
    --leaf: #99cc5f;
    --leaf-faint: #f3f7ee;
    --ink: #2b2b2b;
    --paper: #ffffff;
    --backdrop: #e4e5e7;
  }
  * { box-sizing: border-box; margin: 0; padding: 0; }
  html, body { width: 1200px; height: 442px; overflow: hidden; }
  body {
    background: var(--backdrop);
    position: relative;
    font-family: "Lato", sans-serif;
    color: var(--ink);
  }
  .card {
    position: absolute;
    top: 71px;
    width: 523px;
    height: 299px;
    overflow: hidden;
  }
  .card--front { left: 69px; background: var(--paper); }
  .card--back { left: 608px; background: var(--leaf); }

  /* front */
  .front-deco {
    position: absolute;
    left: 310px; top: 45px;
    width: 300px; height: 300px;
    border-radius: 50%;
    background: var(--sky-faint);
  }
  .front-deco--leaf {
    left: 310px; top: 145px;
    background: var(--leaf-faint);
  }
  .brand {
    position: absolute;
    display: flex;
    align-items: center;
    gap: 20px;
  }
  .brand__dot { border-radius: 50%; flex: none; }
  .brand__name {
    font-family: "Raleway", sans-serif;
    font-weight: 400;
    white-space: nowrap;
  }
  .card--front .brand { left: 37px; top: 40px; }
  .card--front .brand__dot { width: 54px; height: 54px; background: var(--sky); }
  .card--front .brand__name { font-size: 30px; color: var(--ink); }

  .person { position: absolute; left: 36px; top: 191px; }
  .person__name { font-size: 19px; font-weight: 700; color: var(--sky); line-height: 1.2; }
  .person__role { font-size: 12px; font-weight: 700; font-style: italic; margin-top: 3px; }
  .person__quals { font-size: 10.5px; line-height: 1.35; margin-top: 2px; }

  .contacts { position: absolute; left: 325px; top: 193px; list-style: none; }
  .contacts li {
    display: flex; align-items: center; gap: 8px;
    font-size: 11px; height: 18px; margin-bottom: 5.5px;
  }
  .contacts svg { width: 18px; height: 18px; flex: none; }

  .front-band {
    position: absolute; left: 0; bottom: 0;
    width: 100%; height: 16px; background: var(--leaf);
  }
  .front-band__accent {
    position: absolute; right: 0; bottom: 0;
    width: 155px; height: 16px; background: var(--sky);
    clip-path: polygon(12px 0, 100% 0, 100% 100%, 0 100%);
  }

  /* back */
  .back-mark {
    position: absolute;
    left: 272px; top: 17px;
    width: 320px; height: 320px;
    border-radius: 50%;
    background: var(--sky);
    box-shadow: 0 0 0 8px var(--paper);
  }
  .card--back .brand { left: 36px; top: 213px; gap: 14px; }
  .card--back .brand__dot { width: 48px; height: 48px; background: var(--paper); }
  .card--back .brand__name { font-size: 26px; color: var(--paper); letter-spacing: 0.5px; }
</style>
</head>
<body>
  <section class="card card--front">
    <div class="front-deco"></div>
    <div class="front-deco front-deco--leaf"></div>

    <div class="brand">
      <span class="brand__dot"></span>
      <span class="brand__name">Thrive Lane</span>
    </div>

    <div class="person">
      <p class="person__name">Dara Whelby</p>
      <p class="person__role">Counsellor &amp; Psychotherapist</p>
      <p class="person__quals">BSc (Psychol.), BA, Dip. (Couns. &amp; Psych.),<br>PG.Cert (CBT), FGTrK, ONRE</p>
    </div>

    <ul class="contacts">
      <li>
        <svg viewBox="0 0 18 18" aria-hidden="true"><circle cx="9" cy="9" r="9" fill="var(--sky)"/><rect x="6" y="4" width="6" height="10" rx="1.2" fill="none" stroke="#fff" stroke-width="1.2"/></svg>
        000 0000 0000
      </li>
      <li>
        <svg viewBox="0 0 18 18" aria-hidden="true"><circle cx="9" cy="9" r="9" fill="var(--sky)"/><rect x="4.5" y="6" width="9" height="6.5" fill="none" stroke="#fff" stroke-width="1.1"/><path d="M4.5 6 L9 10 L13.5 6" fill="none" stroke="#fff" stroke-width="1.1"/></svg>
        hello@thrivelane.com
      </li>
      <li>
        <svg viewBox="0 0 18 18" aria-hidden="true"><circle cx="9" cy="9" r="9" fill="var(--sky)"/><g fill="none" stroke="#fff" stroke-width="1"><circle cx="9" cy="9" r="5"/><ellipse cx="9" cy="9" rx="2.2" ry="5"/><path d="M4 9 H14 M5 6.5 H13 M5 11.5 H13"/></g></svg>
        thrivelane.com
      </li>
    </ul>

    <div class="front-band"><div class="front-band__accent"></div></div>
  </section>

  <section class="card card--back">
    <div class="back-mark"></div>
    <div class="brand">
      <span class="brand__dot"></span>
      <span class="brand__name">Thrive Lane</span>
    </div>
  </section>
</body>
</html>
```